Wordpress Design Project for Employee Communications Site

We need a Wordpress design for a company that strategizes on and produces materials for employee communications. Improving employee communications at all levels of an organization can help improve overall company performance and results. The site needs to look very clean and professional; we're not afraid of white space. We like the functionality that Wordpress provides; however, we only want one "true" blog page; the other pages should give the impression of a more "static" web site - particularly the home page. I have a logo that I can provide.

I have added these comments to the discussion page:
Great question - thank you for asking it. I’ve done more research

I like the very clean and monochromatic looks to many of these. I don’t have to have monochromatic, but I do like minimal colors. Simple, clean, organized. The home page should “fit” almost entirely without scrolling. I do like fat footers that you can scroll down to. I don’t want a colored background, but any that I’ve chosen with colored backgrounds could be switched to a white background.

http://www.mirabelquennet.example/
http://pondraft.example/
http://v1.samplumworth.example/
http://howdythegoat.example/
http://stayingbrisk.example/
http://www.interiors.kelmun.example/
http://trelvmasters.example/

These last two are more corporate sites. The first one is from a well-respected consultant in my area who does a lot of what I do. And I think Harwenby does a nice job with their site. So, I want to marry the look I like with getting the content job done.

http://www.messagefuelbox.example/
http://www.harwenby.example/view/en_US/us/index.htm

Target Market(s)

Target market is mid- to large-sized companies. More than 500 employees.

Industry/Entity Type

Communications

Requirements
Must have
• Need an impactful home page. There should be a "blog" page; contact us; services; about. For starters, at least. I want fonts to be very readable - that is, either quite dark gray or black.
Nice to have
• I am loathe to include a picture of myself, but I do want some images that say, "professional" and "expert" in communications.
Should not have
• I don't want a hits counter :) (I know no one would do that!).

```html
<!DOCTYPE html>
<html lang="en">
<head>
<meta charset="utf-8">
<title>MWM — Meridian Workplace Messaging Company</title>
<link rel="stylesheet" href="https://fonts.googleapis.com/css2?family=PT+Sans+Narrow:wght@400;700&family=Ubuntu:wght@400;500;700&family=Open+Sans:wght@400&display=swap">
<style>
:root{
  --lime:#c2d93b;
  --lime-pale:#e4edb0;
  --sky:#5fc3e8;
  --ink:#222;
  --text:#444;
  --rule:#d6d6d6;
  --purple:#5a4d7a;
  --white:#fff;
}
*{box-sizing:border-box;margin:0;padding:0}
html,body{width:1200px;height:1052px;overflow:hidden;background:var(--white)}
body{position:relative;font-family:"Ubuntu",sans-serif;color:var(--text)}
.top-band{position:absolute;left:0;top:0;width:1200px;height:10px;background:var(--lime)}
.brand{position:absolute;left:177px;top:64px;width:290px}
.brand-row{display:flex;align-items:center;gap:16px}
.brand-dot{width:56px;height:56px;border-radius:50%;background:var(--sky)}
.brand-name{font-family:"Open Sans",sans-serif;font-size:58px;line-height:60px;color:var(--lime);letter-spacing:1px}
.brand-tag{margin-top:8px;font-family:"Open Sans",sans-serif;font-size:12.5px;color:var(--purple);white-space:nowrap}
.main-nav{position:absolute;left:595px;top:89px;width:520px;height:47px;border-top:1px solid var(--rule);border-bottom:1px solid var(--rule)}
.main-nav ul{list-style:none;position:relative;height:100%}
.main-nav li{position:absolute;top:0;font-family:"Open Sans",sans-serif;font-size:14.5px;color:var(--ink);line-height:45px;white-space:nowrap}
.main-nav li.active{top:-6px;width:66px;height:57px;line-height:57px;text-align:center;background:var(--lime-pale)}
.hero-art{position:absolute;left:190px;top:170px;width:860px;height:370px;border-radius:18px;background:radial-gradient(ellipse at 50% 55%,#f2f2f2 0%,#e4e4e4 55%,#fff 100%)}
.slide-arrow{position:absolute;top:340px}
.slide-arrow.prev{left:148px}
.slide-arrow.next{left:1058px}
.hero-caption{position:absolute;left:390px;top:516px;width:318px;height:47px;border-top:1px solid var(--rule);border-bottom:1px solid var(--rule);background:var(--white);text-align:center;font-family:"PT Sans Narrow",sans-serif;font-size:31px;line-height:45px;color:var(--ink)}
.slide-dots{position:absolute;left:942px;top:553px;display:flex;gap:7px}
.slide-dots span{width:12px;height:12px;border-radius:50%;background:#9a9a9a}
.slide-dots span.on{background:var(--sky)}
.feature{position:absolute;width:227px}
.feature h2{font-family:"PT Sans Narrow",sans-serif;font-weight:700;font-size:22px;color:#333;line-height:24px;margin-bottom:8px;letter-spacing:-.2px;white-space:nowrap}
.feature p{font-size:12px;line-height:15.6px;color:var(--text)}
.feature p span{display:block;white-space:nowrap;text-align:justify;text-align-last:justify;letter-spacing:.5px}
.feature p span.last{text-align-last:left}
.feature .attribution{margin-top:3px;text-align:right;font-weight:700;font-size:11.5px;line-height:14.5px;color:#333}
.read-more{display:flex;align-items:center;gap:4px;margin-top:12px;font-size:12px;font-weight:700;color:var(--ink)}
.read-more i{display:inline-flex}
.read-more i b{width:12px;height:12px;border-radius:50%;display:block}
.read-more i b:first-child{background:var(--sky)}
.read-more i b:last-child{background:var(--lime);margin-left:-3px}
.col-rule{position:absolute;width:1px;background:#e6e6e6}
.footer{position:absolute;left:0;top:984px;width:1200px;height:68px;border-top:6px solid var(--lime-pale);background:linear-gradient(#f4f4f4,#fff)}
.footer-brand{position:absolute;left:210px;top:10px;display:flex;align-items:center;gap:6px;font-family:"Open Sans",sans-serif;font-size:26px;color:#999}
.footer-brand span.dot{width:22px;height:22px;border-radius:50%;background:#bbb}
.footer-nav{position:absolute;left:424px;top:12px;font-family:"Open Sans",sans-serif;font-size:13px;color:var(--ink);white-space:nowrap}
.footer-nav em{font-style:normal;margin:0 14px}
.copyright{position:absolute;left:441px;top:43px;font-family:Arial,sans-serif;font-size:10.5px;color:var(--ink);white-space:nowrap}
.social{position:absolute;left:941px;top:10px;display:flex}
.social span{width:40px;height:40px;border-radius:50%}
.social .one{background:var(--sky)}
.social .two{background:var(--lime);margin-left:-11px}
</style>
</head>
<body>
<div class="top-band"></div>

<header>
  <div class="brand">
    <div class="brand-row"><span class="brand-dot"></span><span class="brand-name">MWM</span></div>
    <div class="brand-tag">Meridian Workplace Messaging Company</div>
  </div>
  <nav class="main-nav">
    <ul>
      <li class="active" style="left:25px">HOME</li>
      <li style="left:121px">ABOUT</li>
      <li style="left:209px">SERVICES</li>
      <li style="left:312px">BLOG</li>
      <li style="left:390px">CONTACT US</li>
    </ul>
  </nav>
</header>

<section class="hero">
  <div class="hero-art" role="img" aria-label="Illustration of three white figures in circles: one on the phone, one with a headset at a laptop, one cheering, linked by curved arrows"></div>
  <svg class="slide-arrow prev" width="38" height="42" viewBox="0 0 38 42"><polygon points="38,0 24,0 0,21 24,42 38,42 14,21" fill="var(--lime)"/></svg>
  <svg class="slide-arrow next" width="38" height="42" viewBox="0 0 38 42"><polygon points="0,0 14,0 38,21 14,42 0,42 24,21" fill="var(--lime)"/></svg>
  <div class="hero-caption">Effective Communication</div>
  <div class="slide-dots"><span class="on"></span><span></span><span></span><span></span></div>
</section>

<main>
  <div class="col-rule" style="left:461px;top:628px;height:110px"></div>
  <div class="col-rule" style="left:738px;top:628px;height:110px"></div>
  <div class="col-rule" style="left:461px;top:826px;height:110px"></div>
  <div class="col-rule" style="left:740px;top:826px;height:110px"></div>

  <article class="feature" style="left:209px;top:607px">
    <h2>External Communication</h2>
    <p><span>Effective communication in the work-</span><span>place is the backbone of any business.</span><span>Without it, you could miss out on</span><span>important opportunities, waste time</span><span>and cause your employees and custom-</span><span class="last">ers to become frustrated.</span></p>
    <div class="read-more"><i><b></b><b></b></i>Read More</div>
  </article>
  <article class="feature" style="left:488px;top:607px">
    <h2>Business Growth</h2>
    <p><span>Effective communication in the work-</span><span>place is the backbone of any business.</span><span>Without it, you could miss out on</span><span>important opportunities, waste time</span><span>and cause your employees and custom-</span><span class="last">ers to become frustrated.</span></p>
    <div class="read-more"><i><b></b><b></b></i>Read More</div>
  </article>
  <article class="feature" style="left:765px;top:607px">
    <h2>Internal Communication</h2>
    <p><span>Effective communication in the work-</span><span>place is the backbone of any business.</span><span>Without it, you could miss out on</span><span>important opportunities, waste time</span><span>and cause your employees and custom-</span><span class="last">ers to become frustrated.</span></p>
    <div class="read-more"><i><b></b><b></b></i>Read More</div>
  </article>

  <article class="feature" style="left:209px;top:803px">
    <h2>What Customers are Saying...</h2>
    <p><span class="last">MWM is a great benchmarking tool."The</span><span>MWM channels offer a very effective</span><span>way to communicate with geographi-</span><span>cally distributed stores and in a retail</span><span class="last">environment."</span></p>
    <div class="attribution">Lorna Vetterby<br>Internal Communications<br>Manager</div>
  </article>
  <article class="feature" style="left:488px;top:803px">
    <h2>Internal Social Media</h2>
    <p><span class="last">MWM is a great benchmarking tool."The</span><span>MWM channels offer a very effective</span><span>way to communicate with geographi-</span><span>cally distributed stores and in a retail</span><span class="last">environment."</span></p>
    <div class="attribution">Specifically for employee<br>communication</div>
  </article>
  <article class="feature" style="left:765px;top:803px">
    <h2>Business Growth</h2>
    <p><span class="last">MWM is a great benchmarking tool."The</span><span>MWM channels offer a very effective</span><span>way to communicate with geographi-</span><span>cally distributed stores and in a retail</span><span class="last">environment."</span></p>
    <div class="attribution">Specifically for employee<br>communication</div>
  </article>
</main>

<footer class="footer">
  <div class="footer-brand"><span class="dot"></span>MWM</div>
  <nav class="footer-nav">Home<em>|</em>About<em>|</em>Services<em>|</em>Blog<em>|</em>Contact Us</nav>
  <div class="copyright">All rights reserved. © Meridian Workplace Messaging Company 2008</div>
  <div class="social"><span class="one"></span><span class="two"></span></div>
</footer>
</body>
</html>
```